Stationery for Villa Marenta Design Hotel**

Who we are:

Wander on an isolated beach while breathing in the fresh, salty, sea air. Listen to the warm Pacific wind rustling through green palm trees as you walk to a pristine lagoon. Feel the delicious warmth of the sun kiss your skin; the beach is yours. At Villa Marenta you can experience a vacation in undisturbed, natural beauty. We have created a place for you to find new strength, relaxation, and inner harmony. We offer total rest to the experienced traveler from all over the world.

We are a brand new and smartly built design-hotel (under construction) close to a unique beach and a fantastic surf spot in Huatulco, Southwest Mexico.

As you can see in the attachments, we do have an established corporate design, but as for now still need a format for booklets for information around our hotel and things to do in the area, important numbers (we fill in the content for that one).

Our corporate colors:
green #64b445, brown #b07043, blue #0ab7cf, yellow # f9b02a and #fcc01a, navy #444f69
Corporate fonts:
Krub and Miller Banner.
For further information access:
www.villamarenta.example
https://slidevault.example/view/QmPxLwZrTyKsNbVcHdJe/

Social Media: VillaMarenta

Industry/Entity Type

Hotel

Font styles to use
Other font styles liked:
• Krub, Miller Banner

Requirements
Must have
• Stick to Logo Design, defined corporate elements, logo, colors, fonts and general touch and feel
Nice to have
• Who we are:

Our corporate colors:
Corporate fonts:
Krub and Miller Banner.
www.villamarenta.example

Social Media: VillaMarenta

```html
<!DOCTYPE html>
<html lang="en">
<head>
<meta charset="utf-8">
<title>Villa Marenta Letterhead</title>
<link href="https://fonts.googleapis.com/css2?family=Krub:wght@500&family=Gelasio:wght@400&display=swap" rel="stylesheet">
<style>
  :root {
    --backdrop: #d9dcdd;
    --paper: #ffffff;
    --teal-deep: #127f80;
    --teal: #17b3b7;
    --teal-light: #6fdde3;
    --teal-pale: #c8f1f3;
    --gold: #e3a81c;
    --text-teal: #137e86;
    --text-grey: #6f7275;
    --rule: #cfd6d7;
  }
  * { margin: 0; padding: 0; box-sizing: border-box; }
  html, body {
    width: 1200px; height: 784px; overflow: hidden;
    background: var(--backdrop);
  }
  .letterhead {
    position: absolute; left: 90px; top: 42px;
    width: 1020px; height: 700px;
    background: var(--paper);
    box-shadow: 0 6px 18px rgba(0,0,0,0.12);
    overflow: hidden;
  }
  .header-band {
    position: absolute; left: 0; top: 0; width: 100%; height: 64px;
    background: linear-gradient(90deg, var(--teal-pale) 0%, var(--teal-light) 35%, var(--teal) 70%, var(--teal-deep) 100%);
  }
  .logo-tab {
    position: absolute; right: 40px; top: 18px;
    width: 250px; height: 96px;
    background: var(--paper);
    border-radius: 16px 16px 0 0;
    display: flex; align-items: center; justify-content: center; gap: 12px;
  }
  .logo-mark {
    flex: none;
    width: 18px; height: 18px; border: 2px solid var(--gold);
  }
  .logo-name {
    font-family: "Krub", sans-serif; font-weight: 500;
    font-size: 21px; letter-spacing: 2px; text-transform: uppercase;
    white-space: nowrap;
    color: var(--gold);
  }
  .contact-block {
    position: absolute; right: 56px; top: 230px;
    padding-left: 18px;
    border-left: 1px solid var(--rule);
    font-family: "Gelasio", Georgia, serif;
    font-style: normal; font-weight: 400;
    font-size: 15px; line-height: 22px;
    white-space: nowrap;
  }
  .contact-row { display: flex; align-items: flex-start; gap: 8px; }
  .contact-row svg { flex: none; margin-top: 4px; }
  .address { color: var(--text-teal); }
  .detail { color: var(--text-grey); }
</style>
</head>
<body>
  <main class="letterhead">
    <div class="header-band"></div>
    <div class="logo-tab">
      <span class="logo-mark"></span>
      <span class="logo-name">Villa Marenta</span>
    </div>
    <address class="contact-block">
      <div class="contact-row address">
        <svg width="14" height="14" viewBox="0 0 14 14"><circle cx="7" cy="7" r="6.5" fill="#17b3b7"/><path d="M7 3.5a2.3 2.3 0 0 0-2.3 2.3C4.7 7.6 7 10.5 7 10.5s2.3-2.9 2.3-4.7A2.3 2.3 0 0 0 7 3.5z" fill="#fff"/></svg>
        <span>Villa Marenta, Playa Serena,<br>Costa Lumbre, Marisol, Mexiko</span>
      </div>
      <div class="contact-row detail">
        <svg width="14" height="14" viewBox="0 0 14 14"><circle cx="7" cy="7" r="6.5" fill="#17b3b7"/><path d="M5 3.8l1.2 1.8-.8.8c.5 1 1.2 1.7 2.2 2.2l.8-.8 1.8 1.2-.7 1.2C6.8 10 4 7.2 3.8 4.5z" fill="#fff"/></svg>
        <span>+52 1 (555) 014 3927</span>
      </div>
      <div class="contact-row detail">
        <svg width="14" height="14" viewBox="0 0 14 14"><circle cx="7" cy="7" r="6.5" fill="#17b3b7"/><rect x="3.8" y="4.8" width="6.4" height="4.4" fill="#fff"/><path d="M3.8 4.8L7 7.3l3.2-2.5" stroke="#17b3b7" stroke-width="0.8" fill="none"/></svg>
        <span>hello@villamarenta.example</span>
      </div>
      <div class="contact-row detail">
        <svg width="14" height="14" viewBox="0 0 14 14"><circle cx="7" cy="7" r="6.5" fill="#17b3b7"/><circle cx="7" cy="7" r="3.4" fill="none" stroke="#fff" stroke-width="0.9"/><path d="M3.6 7h6.8M7 3.6c-1.5 2-1.5 4.8 0 6.8M7 3.6c1.5 2 1.5 4.8 0 6.8" stroke="#fff" stroke-width="0.8" fill="none"/></svg>
        <span>www.villamarenta.example</span>
      </div>
    </address>
  </main>
</body>
</html>
```